KDWB Business Card

Looking for a business card design to incorporate our branding. We want to only use the colors listing in the Branding Package (attached).
Updates

Target Market(s)

People who need their phone or device fixed.

Industry/Entity Type

Electronics

Contact Information for Business Card

Please use:

Brightwick Gadget Clinic LLC
4810 E Harlow Ridge Rd
Suite 417
San Antonio, TX 78163

Marcus Delgrove, Store Manager

(210) 555-0147

Requirements
Must have
• Must include the colors that are contained within the Branding Package PDF file.

```html
<!DOCTYPE html>
<html lang="en">
<head>
<meta charset="utf-8">
<title>Brightwick Gadget Clinic – Business Card</title>
<link href="https://fonts.googleapis.com/css2?family=Arimo:wght@400;700&display=swap" rel="stylesheet">
<style>
  :root {
    --bg: #d8d8da;
    --card-white: #ffffff;
    --card-black: #1c1c1c;
    --brand-orange: #e8411a;
    --brand-lime: #c6d43a;
    --photo-blue: #2f6fd0;
    --photo-skin: #c79a82;
    --text-light: #f2f2f2;
    --text-dark: #333333;
  }
  * { box-sizing: border-box; margin: 0; padding: 0; }
  html, body { width: 1200px; height: 941px; overflow: hidden; }
  body {
    background: var(--bg);
    font-family: "Arimo", Arial, sans-serif;
    position: relative;
  }
  .card {
    position: absolute;
    background: var(--card-white);
    box-shadow: 0 4px 14px rgba(0,0,0,0.18);
    overflow: hidden;
  }
  /* Front card (portrait) */
  .card-front { left: 150px; top: 170px; width: 340px; height: 600px; }
  .brand-row {
    height: 96px;
    display: flex;
    align-items: center;
    justify-content: center;
    gap: 10px;
  }
  .brand-square {
    width: 26px; height: 26px;
    background: var(--brand-orange);
    border-radius: 5px;
  }
  .brand-name {
    color: var(--brand-orange);
    font-size: 19px;
    font-weight: 400;
    letter-spacing: 0.2px;
  }
  .front-photo {
    position: absolute;
    left: 0; top: 96px;
    width: 340px; height: 210px;
    background: linear-gradient(160deg, #eef1f4 0%, #b9c7dd 30%, var(--photo-blue) 55%, #2a5fb8 100%);
  }
  .front-wave { position: absolute; left: 0; top: 250px; width: 340px; height: 90px; }
  .front-info {
    position: absolute;
    left: 0; top: 330px;
    width: 340px; height: 270px;
    background: var(--card-black);
    color: var(--text-light);
    padding: 8px 30px 0 30px;
  }
  .person-name { font-size: 19px; font-weight: 700; margin-bottom: 16px; }
  .address { font-size: 14px; line-height: 18px; margin-bottom: 26px; }
  .contact-list { list-style: none; font-size: 14px; line-height: 26px; }
  .contact-list li { display: flex; align-items: center; gap: 12px; }
  .contact-icon {
    width: 14px; height: 14px;
    background: var(--brand-orange);
    display: inline-flex; align-items: center; justify-content: center;
  }
  /* Back card (landscape) */
  .card-back { left: 540px; top: 300px; width: 600px; height: 345px; }
  .back-photo {
    position: absolute; inset: 0;
    background: radial-gradient(ellipse at 40% 55%, rgba(200,205,215,0.35) 0%, rgba(255,255,255,0) 60%);
  }
  .back-brand {
    position: absolute; inset: 0;
    display: flex; align-items: center; justify-content: center; gap: 18px;
  }
  .back-brand .brand-square { width: 56px; height: 56px; border-radius: 10px; }
  .back-brand .brand-name { font-size: 38px; }
</style>
</head>
<body>

<section class="card card-front">
  <div class="brand-row">
    <span class="brand-square"></span>
    <span class="brand-name">Brightwick Gadget Clinic</span>
  </div>
  <div class="front-photo" role="img" aria-label="Photo of hands repairing a smartphone on a blue work mat"></div>
  <svg class="front-wave" viewBox="0 0 340 90" preserveAspectRatio="none" aria-hidden="true">
    <path d="M0 10 Q170 70 340 70 L340 90 L0 90 Z" fill="var(--brand-orange)"/>
    <path d="M0 18 Q170 78 340 80 L340 90 L0 90 Z" fill="var(--card-black)"/>
  </svg>
  <div class="front-info">
    <h1 class="person-name">Marcus Delgrove</h1>
    <p class="address">4810 E Harlow Ridge Rd<br>Suite 417<br>San Antonio, TX 78163</p>
    <ul class="contact-list">
      <li><span class="contact-icon">
        <svg width="10" height="10" viewBox="0 0 10 10"><path d="M2 1 L4 1 L4.5 3 L3.5 4 Q4.5 6 6 6.5 L7 5.5 L9 6 L9 8 Q5 9 2 5 Q1 3 2 1Z" fill="#fff"/></svg>
      </span>(210) 555-0147</li>
      <li><span class="contact-icon">
        <svg width="10" height="10" viewBox="0 0 10 10"><rect x="1" y="2.5" width="8" height="5.5" fill="none" stroke="#fff" stroke-width="1"/><path d="M1 2.5 L5 5.5 L9 2.5" fill="none" stroke="#fff" stroke-width="1"/></svg>
      </span>marcus@BrightwickClinic.com</li>
      <li><span class="contact-icon">
        <svg width="10" height="10" viewBox="0 0 10 10"><circle cx="5" cy="5" r="3.6" fill="none" stroke="#fff" stroke-width="1"/><path d="M1.4 5 H8.6 M5 1.4 Q3 5 5 8.6 M5 1.4 Q7 5 5 8.6" fill="none" stroke="#fff" stroke-width="0.8"/></svg>
      </span>www.BrightwickClinic.com</li>
    </ul>
  </div>
</section>

<section class="card card-back">
  <div class="back-photo" role="img" aria-label="Faint photo of a smartphone being repaired"></div>
  <div class="back-brand">
    <span class="brand-square"></span>
    <span class="brand-name">Brightwick Gadget Clinic</span>
  </div>
</section>

</body>
</html>
```